Hunting Ethics Organization Needs a Web Design with Logo Refresh

This project involves the creation of a website design including the homepage design, inside page design, and logo refinements. Our organization is Tessaly, and we are a not-for-profit hunting ethics organization.
The focus of the new website design is to bring attention the mission of our organization, provide an overview of the areas where our organization deploys its resources to support the modern hunter, and to encourage visitors to support our organization by donating in support of the organization’s mission.
The winning design will be implemented in Wordpress by our in-house team. If you have questions about how any particular design element may translate to Wordpress, please feel free to post questions in response to this brief. In general, however, we’re more focused on the evolution and delivery of a strong overall design aesthetic – we’ll shoulder the responsibility of how we translate that design into Wordpress.
See attached design brief for full details.

```html
<!DOCTYPE html>
<html lang="en">
<head>
<meta charset="utf-8">
<title>Tessaly – Protect the Future of Hunting</title>
<link rel="stylesheet" href="https://fonts.googleapis.com/css2?family=Open+Sans:wght@300;400;600;700&display=swap">
<style>
:root{
  --olive:#a9a25a;
  --olive-dark:#958e48;
  --beige:#ecebd6;
  --ink:#3d3d3d;
  --muted:#6f6f6f;
  --blue:#2c5e9a;
  --white:#ffffff;
  --footer:#4a4745;
  --footer-bottom:#3b3937;
  --footer-text:#cfccc4;
}
*{box-sizing:border-box;margin:0;padding:0}
html,body{width:1200px;height:3233px;overflow:hidden}
body{font-family:"Open Sans",Arial,sans-serif;color:var(--ink);background:var(--white);position:relative}
.abs{position:absolute}

/* header */
.site-header{position:absolute;left:0;top:0;width:1200px;height:102px;background:var(--white)}
.brand{position:absolute;left:146px;top:24px;display:flex;align-items:center;gap:10px}
.brand-dot{width:24px;height:24px;border-radius:50%;background:var(--olive)}
.brand-name{font-size:38px;font-weight:700;color:var(--blue);letter-spacing:1px;line-height:1}
.main-nav{position:absolute;right:243px;top:60px;display:flex;gap:24px;font-size:12.5px;letter-spacing:.4px;color:#555;text-transform:uppercase;white-space:nowrap;line-height:16px}
.btn{display:inline-block;background:var(--olive);color:var(--white);font-weight:600;text-transform:uppercase;letter-spacing:1px;text-align:center}
.header-donate{position:absolute;left:974px;top:54px;width:97px;height:28px;line-height:28px;font-size:12.5px}

/* hero */
.hero{position:absolute;left:0;top:102px;width:1200px;height:554px;
  background:linear-gradient(180deg,#0f1a2e 0%,#243049 30%,#5a4a55 52%,#b9683a 70%,#d9823c 78%,#3a2a22 88%,#120f0f 100%)}
.hero-title{position:absolute;left:0;width:1200px;top:152px;font-size:86px;font-weight:300;color:var(--white);letter-spacing:42px;text-indent:42px;text-align:center;line-height:1}
.hero-rule{position:absolute;left:343px;top:265px;width:512px;height:2px;background:rgba(255,255,255,.75)}
.hero-sub{position:absolute;left:0;width:1200px;top:291px;font-size:32px;color:var(--white);text-align:center;letter-spacing:1px;line-height:44px}

/* sections */
.section-title{font-size:24px;color:var(--olive);text-transform:uppercase;letter-spacing:1.5px;font-weight:400;text-align:center}
.lead{font-size:12.5px;line-height:22px;color:var(--muted);text-align:center}

.mission{position:absolute;left:0;top:656px;width:1200px;height:523px;background:var(--beige)}
.pillar{position:absolute;width:300px;text-align:center}
.pillar svg{display:block;margin:0 auto}
.pillar h3{font-size:19px;font-weight:400;color:#444;text-transform:uppercase;letter-spacing:.5px;margin-top:50px}
.pillar p{font-size:12.5px;line-height:22px;color:var(--muted);margin-top:12px}

.work{position:absolute;left:0;top:1179px;width:1200px;height:919px;background:var(--white)}
.arrows{position:absolute;display:flex;gap:8px}
.arrow{width:22px;height:22px;border:1.5px solid #aaa;border-radius:50%;display:flex;align-items:center;justify-content:center}
.work-grid{position:absolute;left:181px;top:205px;width:836px;display:grid;grid-template-columns:repeat(3,1fr);gap:3px}
.work-card{background:var(--beige);height:315px}
.work-card h4{height:51px;line-height:51px;font-size:12.5px;font-weight:400;color:var(--olive-dark);text-align:center;text-transform:uppercase;letter-spacing:.6px}
.work-photo{height:194px}
.work-card p{height:70px;line-height:70px;font-size:12px;color:var(--muted);text-align:center}

.news{position:absolute;left:0;top:2098px;width:1200px;height:459px;background:var(--beige)}
.news-grid{position:absolute;left:181px;top:132px;width:836px;display:grid;grid-template-columns:repeat(3,1fr);gap:12px}
.news-card{background:var(--white);height:284px}
.news-photo{height:116px}
.news-body{padding:14px 12px 0 12px}
.news-body h4{font-size:20px;font-weight:400;color:#333}
.news-meta{font-size:11.5px;color:#888;margin-top:4px;display:flex;align-items:center;gap:6px}
.news-body p{font-size:12.5px;line-height:20px;color:var(--muted);margin-top:8px;text-align:justify}

.support{position:absolute;left:0;top:2557px;width:1200px;height:334px;background:var(--white)}
.support-title{position:absolute;left:0;top:88px;width:1200px;font-size:23px;font-weight:400;color:#333;text-transform:uppercase;letter-spacing:1.5px;text-align:center}
.support-donate{position:absolute;left:553px;top:234px;width:100px;height:28px;line-height:28px;font-size:12.5px}

/* footer */
.site-footer{position:absolute;left:0;top:2891px;width:1200px;height:259px;background:var(--footer)}
.foot-col{position:absolute;top:50px}
.foot-col h5{font-size:14px;font-weight:600;color:var(--white);letter-spacing:1px;text-transform:uppercase}
.foot-col h5::after{content:"";display:block;width:36px;height:2px;background:var(--olive);margin-top:8px}
.foot-col ul{list-style:none;margin-top:12px}
.foot-col li{font-size:12.5px;line-height:19px;color:var(--footer-text)}
.foot-col p{font-size:12.5px;line-height:19px;color:var(--footer-text);margin-top:12px;width:290px}
.newsletter{position:absolute;left:782px;top:157px;width:291px;height:35px;display:flex}
.newsletter span{flex:1;background:var(--white);font-size:11.5px;color:#999;line-height:35px;padding-left:12px}
.newsletter b{width:86px;background:var(--olive);color:var(--white);font-size:12.5px;line-height:35px;text-align:center;letter-spacing:1px}
.footer-bottom{position:absolute;left:0;top:3150px;width:1200px;height:83px;background:var(--footer-bottom)}
.copyright{position:absolute;left:129px;top:33px;font-size:12px;color:var(--footer-text)}
.copyright em{font-style:normal;color:var(--olive)}
.legal{position:absolute;left:618px;top:33px;font-size:12px;color:var(--footer-text);display:flex;gap:14px;text-transform:uppercase}
.social{position:absolute;left:928px;top:29px;display:flex;gap:11px}
.social i{width:22px;height:22px;border-radius:50%;background:#d9d6ce;display:block}
</style>
</head>
<body>

<header class="site-header">
  <div class="brand"><span class="brand-dot"></span><span class="brand-name">Tessaly</span></div>
  <nav class="main-nav">
    <span>About Us</span><span>Hunting Ethics</span><span>Conservation</span><span>Get Involved</span><span>Contact Us</span>
  </nav>
  <span class="btn header-donate">Donate</span>
</header>

<section class="hero" role="img" aria-label="Starry night sky with the milky way over a snow-capped mountain at sunset">
  <h1 class="hero-title">TESSALY</h1>
  <div class="hero-rule"></div>
  <p class="hero-sub">PROTECT THE FUTURE OF HUNTING</p>
</section>

<section class="mission">
  <h2 class="section-title abs" style="left:0;top:100px;width:1200px">Help us protect the future of hunting</h2>
  <p class="lead abs" style="left:150px;top:140px;width:900px">Lorem ipsum dolor sit amet voluptatem fugit aut illo omnis explicabo ipsa nemo enim ipsam quasi illo dolores ut voluptatem doloremque perspiciatis beatae magni architecto odit odit, aspernatur magni quae aperiam aut veritatis beatae eos aut voluptas doloremque perspiciatis</p>

  <div class="pillar" style="left:122px;top:250px">
    <svg width="60" height="80" viewBox="0 0 60 80" fill="none" stroke="#777" stroke-width="2"><path d="M6 4h34l14 14v58H6z"/><path d="M40 4v14h14"/><path d="M16 34h28M16 44h28M16 54h28M16 64h20"/></svg>
    <h3>Hunting Ethics</h3>
    <p>Ipsam ipsa odit aperiam aspernatur veritatis unde enim accusantium laudantiu</p>
  </div>
  <div class="pillar" style="left:449px;top:250px">
    <svg width="80" height="80" viewBox="0 0 80 80" fill="none" stroke="#777" stroke-width="2"><circle cx="40" cy="34" r="24"/><path d="M16 34h48M40 10c-10 12-10 36 0 48M40 10c10 12 10 36 0 48"/><path d="M14 54a30 30 0 0 0 52 0"/><path d="M40 64v8M26 74h28"/></svg>
    <h3>Conservation</h3>
    <p>Ipsam ipsa odit aperiam aspernatur veritatis unde enim accusantium laudantiu</p>
  </div>
  <div class="pillar" style="left:775px;top:250px">
    <svg width="80" height="80" viewBox="0 0 80 80" fill="none" stroke="#777" stroke-width="2"><path d="M40 14a20 20 0 0 0-12 36v10h24V50a20 20 0 0 0-12-36z"/><path d="M30 66h20M32 72h16"/><path d="M40 2v6M14 12l5 5M66 12l-5 5M6 36h6M68 36h6"/></svg>
    <h3>Get Involved</h3>
    <p>Ipsam ipsa odit aperiam aspernatur veritatis unde enim accusantium laudantiu</p>
  </div>
</section>

<section class="work">
  <h2 class="section-title abs" style="left:0;top:100px;width:1200px">What we have done</h2>
  <p class="lead abs" style="left:0;top:138px;width:1200px">quae explicabo dicta quasi lorem ipsum dolor sit amet rem ex aspernatur veritatis</p>
  <div class="arrows" style="left:968px;top:164px">
    <span class="arrow"><svg width="8" height="10" viewBox="0 0 8 10"><path d="M6 1L2 5l4 4" fill="none" stroke="#999" stroke-width="1.6"/></svg></span>
    <span class="arrow"><svg width="8" height="10" viewBox="0 0 8 10"><path d="M2 1l4 4-4 4" fill="none" stroke="#999" stroke-width="1.6"/></svg></span>
  </div>
  <div class="work-grid">
    <article class="work-card"><h4>Quae explicabo dicta quasi</h4><div class="work-photo" role="img" aria-label="Stag standing in an autumn meadow" style="background:linear-gradient(135deg,#6d5a3c,#a88452 55%,#7c6a4a)"></div><p>it amet rem ex aspernatur veritatis</p></article>
    <article class="work-card"><h4>Ipsum dolor voluptatem</h4><div class="work-photo" role="img" aria-label="Hunter in camouflage with a retriever by a marsh" style="background:linear-gradient(135deg,#b9b7a6,#8a7758 55%,#c8a45a)"></div><p>dolor sit amet voluptatem fugit illo omnis</p></article>
    <article class="work-card"><h4>Fugit omnis explicabo</h4><div class="work-photo" role="img" aria-label="Two hunters in camouflage among bare winter trees" style="background:linear-gradient(135deg,#9c9f97,#6b6350 55%,#8d8a80)"></div><p>explicabo ipsa odit nemo enim ipsam quasi</p></article>
    <article class="work-card"><h4>Odit nemo rem ipsam qua</h4><div class="work-photo" role="img" aria-label="Two hunters with a dog walking across a field" style="background:linear-gradient(135deg,#a7a49c,#7b6f5b 55%,#8c7a60)"></div><p>illo dolores ut voluptate odit doloremque</p></article>
    <article class="work-card"><h4>Illo dolores voluptate</h4><div class="work-photo" role="img" aria-label="Hunter in camouflage aiming a shotgun" style="background:linear-gradient(135deg,#cfcfcf,#7a6e5e 50%,#a9a6a0)"></div><p>perspiciatis beatae magni architecto odit</p></article>
    <article class="work-card"><h4>Dolorem perspiciatis</h4><div class="work-photo" role="img" aria-label="Hunter wading through a stream with a dog" style="background:linear-gradient(135deg,#8c8470,#6d6756 50%,#9c9a86)"></div><p>quae aperiam magni ipsam aperiam</p></article>
  </div>
</section>

<section class="news">
  <h2 class="section-title abs" style="left:0;top:80px;width:1200px">Current hunting news</h2>
  <div class="arrows" style="left:968px;top:97px">
    <span class="arrow"><svg width="8" height="10" viewBox="0 0 8 10"><path d="M6 1L2 5l4 4" fill="none" stroke="#999" stroke-width="1.6"/></svg></span>
    <span class="arrow"><svg width="8" height="10" viewBox="0 0 8 10"><path d="M2 1l4 4-4 4" fill="none" stroke="#999" stroke-width="1.6"/></svg></span>
  </div>
  <div class="news-grid">
    <article class="news-card"><div class="news-photo" role="img" aria-label="Deer in a forest at golden sunset" style="background:linear-gradient(180deg,#e8a24a,#b8652a 60%,#3d2a1a)"></div>
      <div class="news-body"><h4>Dolores Architecto</h4><div class="news-meta"><svg width="12" height="10" viewBox="0 0 12 10"><path d="M1 1h10v6H5l-3 2V7H1z" fill="#999"/></svg>180 comments</div>
      <p>Lorem ipsum dolor sit voluptatem fugit illo omnis explicabo ipsa odit nemo quasi illo voluptate odit doloremque perspiciatis beatae magni architecto</p></div></article>
    <article class="news-card"><div class="news-photo" role="img" aria-label="Mountain lake landscape at dusk" style="background:linear-gradient(180deg,#d9c0c4,#9a8f9e 45%,#6b6a5c 70%,#c89a6a)"></div>
      <div class="news-body"><h4>Omnis Explicabo</h4><div class="news-meta"><svg width="12" height="10" viewBox="0 0 12 10"><path d="M1 1h10v6H5l-3 2V7H1z" fill="#999"/></svg>125 comments</div>
      <p>Lorem ipsum dolor sit voluptatem fugit illo omnis explicabo ipsa odit nemo quasi illo voluptate odit doloremque perspiciatis beatae magni architecto</p></div></article>
    <article class="news-card"><div class="news-photo" role="img" aria-label="Hunting dog beside a hunter in a field" style="background:linear-gradient(135deg,#7c6a52,#c0a070 55%,#5e5242)"></div>
      <div class="news-body"><h4>Amet Voluptatem</h4><div class="news-meta"><svg width="12" height="10" viewBox="0 0 12 10"><path d="M1 1h10v6H5l-3 2V7H1z" fill="#999"/></svg>120 comments</div>
      <p>Lorem ipsum dolor sit voluptatem fugit illo omnis explicabo ipsa odit nemo quasi illo voluptate odit doloremque perspiciatis beatae magni architecto</p></div></article>
  </div>
</section>

<section class="support">
  <h2 class="support-title">Support us as we empower the modern hunter</h2>
  <p class="lead abs" style="left:120px;top:134px;width:960px;color:#555">Lorem ipsum dolor sit amet voluptatem fugit aut illo omnis explicabo ipsa nemo enim ipsam quasi illo dolores ut voluptatem doloremque perspiciatis beatae magni architecto odit aspernatur magni quae aperiam aut veritatis beatae eos aut voluptas doloremque perspiciatis error natus nonaquia totame stone dolores consequuntur ut consequuntur architecto sunt beatae architecto aperiam natus.</p>
  <span class="btn support-donate">Donate</span>
</section>

<footer class="site-footer">
  <div class="foot-col" style="left:129px"><h5>Company</h5><ul><li>Who we are</li><li>What we do</li><li>Company profile</li><li>What they say</li><li>Our awesome team</li></ul></div>
  <div class="foot-col" style="left:307px"><h5>Address</h5><ul><li>Pine Ridge Point</li><li>Tower B</li><li>12th Floor</li><li>Cedar Plaza</li><li>Cedar Road</li><li>Austria</li></ul></div>
  <div class="foot-col" style="left:461px"><h5>Support</h5><ul><li>Forum</li><li>FAQ</li><li>Contact</li><li>Chat</li><li>Find Job</li></ul></div>
  <div class="foot-col" style="left:618px"><h5>Other Links</h5><ul><li>Chirper</li><li>Facepage</li><li>Pinwall</li><li>Fieldspot</li><li>RSS</li></ul></div>
  <div class="foot-col" style="left:782px"><h5>Newsletter</h5><p>Lorem ipsum dolor sit amet voluptatem fugit illo omnis explicabo ipsa odit nemo</p></div>
  <div class="newsletter"><span>enter your email</span><b>SEND</b></div>
</footer>

<div class="footer-bottom">
  <p class="copyright">COPYRIGHT © 2015 <em>COMPANY</em>. ALL RIGHTS RESERVED.</p>
  <div class="legal"><span>Term and use</span><span>Privacy policy</span><span>Career</span></div>
  <div class="social"><i></i><i></i><i></i><i></i><i></i></div>
</div>

</body>
</html>
```